Letterhead and matching envelope design for a dental office

We need a new stationary design, letterhead and envelope #10, for a dental office in Denver area. We are called Bright Harbor Dental. We want a simple and minimalistic design but not a boring design. I wish to have one good point that makes it look professional. I have attached our logo. Feel free to use either one. I want the design for letterhead and envelope look like a "matching pair" but not look the same. The envelope doesn't have to be white and it will have an address window on bottom left.

Target Market(s)

everyone who visits dentist (adults)

Industry/Entity Type

Dental

Font styles to use
Other font styles liked:
• close to font on logo or something that matches well

Requirements
Must have
• professional
• simple, minimalistic
• unique point that stands out
Nice to have
• matching but not same design for letterhead and envelope
Should not have
• not look like all the other boring designs
• no flowery, distracting feats

```html
<!DOCTYPE html>
<html lang="en">
<head>
<meta charset="utf-8">
<title>Bright Harbor Dental — Letterhead</title>
<link rel="stylesheet" href="https://fonts.googleapis.com/css2?family=Open+Sans:wght@400;600;700&display=swap">
<style>
  :root {
    --backdrop: #d9d0cc;
    --paper: #ffffff;
    --brand-green: #3bb54a;
    --leaf-tint: #e6f2e0;
    --ink: #555555;
    --ink-dark: #222222;
    --signature-tone: #d6d6d6;
  }
  * { box-sizing: border-box; margin: 0; padding: 0; }
  html, body {
    width: 1200px; height: 784px; overflow: hidden;
    background: var(--backdrop);
    font-family: "Open Sans", Arial, sans-serif;
  }
  .canvas {
    width: 1200px; height: 784px;
    display: flex; align-items: center; justify-content: center;
  }
  .letterhead {
    position: relative;
    width: 523px; height: 740px;
    background: var(--paper);
    overflow: hidden;
  }
  .brand-mark {
    position: absolute; top: 44px; right: 40px;
    display: flex; align-items: center; gap: 8px;
  }
  .brand-mark__dot {
    width: 14px; height: 14px; border-radius: 50%;
    background: var(--brand-green);
  }
  .brand-mark__name {
    font-size: 13px; font-weight: 600; color: var(--brand-green);
    letter-spacing: 0.06em; text-transform: uppercase;
  }
  .letter {
    position: absolute; top: 118px; left: 48px; width: 400px;
    color: var(--ink); font-size: 9.5px; line-height: 1.35;
  }
  .letter__salutation {
    font-weight: 700; color: var(--ink-dark); font-size: 10.5px;
    margin-bottom: 8px;
  }
  .letter__para { margin-bottom: 8px; }
  .signature {
    position: absolute; top: 372px; left: 56px;
    width: 90px; height: 50px;
  }
  .leaf-decor {
    position: absolute; left: 0; bottom: 70px;
    width: 420px; height: 300px;
  }
  .footer {
    position: absolute; left: 0; right: 40px; bottom: 26px;
    text-align: right; font-size: 8.5px; line-height: 1.6; color: var(--ink-dark);
  }
  .footer__name { color: var(--brand-green); font-weight: 700; font-size: 9.5px; }
  .footer__contacts { display: inline-flex; gap: 8px; align-items: center; }
  .footer__item { display: inline-flex; align-items: center; gap: 3px; }
  .footer__icon { width: 9px; height: 9px; }
  .base-band {
    position: absolute; left: 0; right: 0; bottom: 0;
    height: 7px; background: var(--brand-green);
  }
</style>
</head>
<body>
<main class="canvas">
  <article class="letterhead">
    <header class="brand-mark">
      <span class="brand-mark__dot"></span>
      <span class="brand-mark__name">Bright Harbor Dental</span>
    </header>

    <svg class="leaf-decor" viewBox="0 0 420 300" role="img" aria-label="Faint brand decoration in pale green">
      <rect x="20" y="20" width="380" height="260" rx="130" fill="var(--leaf-tint)" opacity="0.7"/>
    </svg>

    <section class="letter">
      <p class="letter__salutation">Dear Mr. Ellis.</p>
      <p class="letter__para">Lorem Ipsum is simply dummy text of the printing and typesetting industry. Lorem Ipsum has been the industry's standard dummy text ever since the 1500s, when an unknown printer took a galley of type and scrambled it to make a type specimen book. It has survived not only five centuries, but also the leap into electronic typesetting, remaining essentially unchanged.</p>
      <p class="letter__para">The standard chunk of Lorem Ipsum used since the 1500s is reproduced below for those interested. Sections 1.10.32 and 1.10.33 from "de Finibus Bonorum et Malorum" by Cicero are also reproduced in their exact original form, accompanied by English versions from the 1914 translation by H. Rackham.</p>
      <p class="letter__para">Lorem Ipsum is simply dummy text of the printing and typesetting industry. Lorem Ipsum has been the industry's standard dummy text ever since the 1500s, when an unknown printer took a galley of type and scrambled it to make a type specimen book. It has survived not only five centuries, but also the leap into electronic typesetting, remaining essentially unchanged. It was popularised in the</p>
    </section>

    <svg class="signature" viewBox="0 0 90 50" role="img" aria-label="Handwritten signature">
      <rect x="0" y="10" width="90" height="30" rx="15" fill="var(--signature-tone)"/>
    </svg>

    <footer class="footer">
      <div class="footer__name">Bright Harbor Dental</div>
      <div class="footer__address">4210 LAKEVIEW BLVD, SUITE 210 ARVADA, CO 80002</div>
      <div class="footer__contacts">
        <span class="footer__item">
          <svg class="footer__icon" viewBox="0 0 10 10" aria-hidden="true"><circle cx="5" cy="5" r="5" fill="var(--brand-green)"/><path d="M3.2 2.6c.3-.3.6-.3.8 0l.5.7c.2.2.1.5-.1.7l-.3.3c.3.6.8 1.1 1.4 1.4l.3-.3c.2-.2.5-.2.7-.1l.7.5c.3.2.3.5 0 .8l-.4.4c-1.6.2-4.1-2.3-3.9-3.9z" fill="#fff"/></svg>
          303-555-0148
        </span>
        <span class="footer__item">
          <svg class="footer__icon" viewBox="0 0 10 10" aria-hidden="true"><circle cx="5" cy="5" r="5" fill="var(--brand-green)"/><rect x="2.5" y="3.3" width="5" height="3.4" fill="none" stroke="#fff" stroke-width="0.7"/><path d="M2.5 3.3L5 5.2l2.5-1.9" fill="none" stroke="#fff" stroke-width="0.7"/></svg>
          info@brightharbordental.com
        </span>
        <span class="footer__item">
          <svg class="footer__icon" viewBox="0 0 10 10" aria-hidden="true"><circle cx="5" cy="5" r="5" fill="var(--brand-green)"/><circle cx="5" cy="5" r="2.6" fill="none" stroke="#fff" stroke-width="0.6"/><path d="M2.4 5h5.2M5 2.4c-1.2 1.4-1.2 3.8 0 5.2M5 2.4c1.2 1.4 1.2 3.8 0 5.2" fill="none" stroke="#fff" stroke-width="0.5"/></svg>
          www.brightharbordental.com
        </span>
      </div>
    </footer>

    <div class="base-band"></div>
  </article>
</main>
</body>
</html>
```